we can communicate on this, but i want to follow the approach we took on Pellew|Marsh & Quinlan but i feel the card front needs the black background and the platinum and gold logo. The back? I am open. we can use the same info from PM&Q. Velmont Arc is an enhanced equity investment fund - basically a very exclusive boutique hedge fund that uses only stock options. very advanced things. hope you are interested

Contact Information for Business Card

Dr. Lewis T. Brennick, CFA
Scientifique de fusée financière
701.555.0143
LTBquant47@mailvantor.com

4718 Willow Creek Bend W.
West Fargo, ND 58078

No web site

Colors

Designer to choose colors to be used in the design.

Requirements
Nice to have
• I tend to prefer the most visible applications of the logo to include logo and name, the logo version with a black background and the gold and platinum components separated by the black. I see this working well for a single side (logo and name - this is card front to me).
• I am fairly open to other treatments on the reverse side with the data. To me, it makes sense to have a different color rendition of the logo on the reverse and it may be a muted black tone on tone or an oversized portion that would have spot UV. Or, the reverse may play with colors and layout
Should not have
• Other colors = no no
• Decorative font

```html
<!DOCTYPE html>
<html lang="en">
<head>
<meta charset="utf-8">
<title>Velmont Arc — Business Card</title>
<link href="https://fonts.googleapis.com/css2?family=Montserrat:wght@600;700&family=Lato:wght@400&display=swap" rel="stylesheet">
<style>
  :root {
    --backdrop: #8a8781;
    --card: #262626;
    --card-hi: #2e2e2e;
    --gold: #c9a93c;
    --white: #f4f4f4;
    --grey: #a3a3a3;
    --rule: #6a6a6a;
  }
  * { margin: 0; padding: 0; box-sizing: border-box; }
  html, body { width: 1200px; height: 985px; overflow: hidden; }
  body {
    background: var(--backdrop);
    display: flex;
    flex-direction: column;
    align-items: center;
    justify-content: center;
    gap: 60px;
  }
  .card {
    width: 700px;
    height: 400px;
    background: linear-gradient(135deg, var(--card-hi), var(--card) 60%);
    box-shadow: 0 10px 24px rgba(0,0,0,.35);
    position: relative;
  }
  /* Front */
  .card-front {
    display: flex;
    flex-direction: column;
    align-items: center;
    justify-content: center;
    gap: 26px;
  }
  .brand-dot {
    width: 110px; height: 110px;
    border-radius: 50%;
    background: var(--gold);
  }
  .brand-name {
    font-family: "Montserrat", sans-serif;
    font-weight: 700;
    font-size: 40px;
    letter-spacing: 2px;
    color: var(--white);
    text-transform: uppercase;
  }
  /* Back */
  .card-back { padding: 40px 48px; }
  .back-brand {
    display: flex; align-items: center; gap: 16px;
  }
  .back-brand .brand-dot { width: 80px; height: 80px; }
  .back-brand .brand-name { font-size: 22px; }
  .holder { position: absolute; left: 48px; top: 178px; width: 470px; }
  .holder-name {
    font-family: "Montserrat", sans-serif;
    font-weight: 600;
    font-size: 27px;
    color: var(--gold);
    text-transform: uppercase;
    letter-spacing: .5px;
  }
  .holder-title {
    font-family: "Lato", sans-serif;
    font-size: 16px;
    color: var(--grey);
    letter-spacing: .6px;
    margin-top: 2px;
    padding-bottom: 14px;
    border-bottom: 1px solid var(--rule);
  }
  .contact-list { list-style: none; margin-top: 16px; }
  .contact-list li {
    display: flex; align-items: center; gap: 12px;
    font-family: "Lato", sans-serif;
    font-size: 16px;
    color: var(--grey);
    letter-spacing: .8px;
    line-height: 30px;
  }
  .contact-list svg { width: 16px; height: 16px; fill: var(--gold); flex: none; }
</style>
</head>
<body>

  <section class="card card-front">
    <div class="brand-dot"></div>
    <div class="brand-name">Velmont Arc</div>
  </section>

  <section class="card card-back">
    <div class="back-brand">
      <div class="brand-dot"></div>
      <div class="brand-name">Velmont Arc</div>
    </div>

    <div class="holder">
      <h1 class="holder-name">Dr. Lewis T. Brennick, CFA</h1>
      <p class="holder-title">Scientifique des Fusées Financières</p>
      <ul class="contact-list">
        <li>
          <svg viewBox="0 0 24 24"><path d="M6.6 10.8a15 15 0 0 0 6.6 6.6l2.2-2.2a1 1 0 0 1 1-.25 11.4 11.4 0 0 0 3.6.6 1 1 0 0 1 1 1V20a1 1 0 0 1-1 1A17 17 0 0 1 3 4a1 1 0 0 1 1-1h3.5a1 1 0 0 1 1 1c0 1.25.2 2.45.6 3.6a1 1 0 0 1-.25 1z"/></svg>
          701.555.0143
        </li>
        <li>
          <svg viewBox="0 0 24 24"><path d="M2 5h20v14H2z M4 7v.5l8 5 8-5V7l-8 5z" fill-rule="evenodd"/></svg>
          LTBquant47@mailvantor.com
        </li>
        <li>
          <svg viewBox="0 0 24 24"><path d="M12 2a7 7 0 0 0-7 7c0 5 7 13 7 13s7-8 7-13a7 7 0 0 0-7-7zm0 9.5A2.5 2.5 0 1 1 12 6.5a2.5 2.5 0 0 1 0 5z"/></svg>
          4718 Willow Creek Bend W., West Fargo, ND 58078
        </li>
      </ul>
    </div>
  </section>

</body>
</html>
```